Marlow Sail Works President Business Card Carbon fiber catamarans

Hi.. I need a new business card design.. I am the President of a high tech yacht builder. We build Carbon Fiber go fast catamarans... Maybe we use the file I am sharing to you as the back of the card.. We need to look cool and crisp ...

Target Market(s)

Affluent People who will purchase a cool yacht

Industry/Entity Type

Custom Yacht Builder

Contact Information for Business Card

Dean Pellway , President, 731.508.2164 USA

Font styles to use
Serif

Requirements
Must have
• the clean crisp cool feel
Nice to have
• clean and crisp
Should not have
• Bold ugly

```html
<!DOCTYPE html>
<html lang="en">
<head>
<meta charset="utf-8">
<title>Marlow Sail Works – Business Card</title>
<link href="https://fonts.googleapis.com/css2?family=Roboto:wght@300;400;500&display=swap" rel="stylesheet">
<style>
  :root {
    --backdrop: #3a3a3c;
    --card: #0b0b0b;
    --ink: #e6e6e6;
    --ink-soft: #bfbfbf;
    --rule: #8a8a8a;
    --silver-light: #f4f4f4;
    --silver-dark: #6e6e6e;
  }
  * { margin: 0; padding: 0; box-sizing: border-box; }
  html, body { width: 1200px; height: 874px; overflow: hidden; }
  body {
    background: var(--backdrop);
    font-family: "Roboto", Arial, sans-serif;
    color: var(--ink);
    position: relative;
  }
  .card {
    position: absolute;
    left: 280px;
    width: 640px;
    height: 366px;
    background: var(--card);
    overflow: hidden;
  }
  .card--front { top: 61px; }
  .card--back { top: 447px; }

  .brand {
    position: absolute;
    display: flex;
    align-items: center;
    gap: 14px;
    color: var(--ink-soft);
    font-weight: 400;
    letter-spacing: 5px;
    text-transform: uppercase;
    white-space: nowrap;
  }
  .brand__dot {
    width: 34px; height: 34px;
    border-radius: 50%;
    background: var(--ink-soft);
    flex: none;
  }
  .card--front .brand { left: 50%; top: 50%; transform: translate(-50%, -50%); font-size: 34px; }
  .card--back .brand { right: 40px; top: 62px; font-size: 26px; }
  .card--back .brand__dot { width: 28px; height: 28px; }

  .person { position: absolute; left: 40px; top: 92px; }
  .person__name { font-size: 21px; font-weight: 500; letter-spacing: 0.5px; text-transform: uppercase; }
  .person__title { font-size: 14px; color: var(--ink-soft); margin-top: 3px; }

  .rule {
    position: absolute;
    left: 40px; right: 80px; top: 148px;
    height: 1px; background: var(--rule);
  }

  .contact { position: absolute; left: 40px; top: 162px; list-style: none; font-size: 14px; line-height: 19px; }
  .contact li { display: flex; align-items: center; gap: 10px; }
  .contact svg { width: 11px; height: 11px; fill: var(--ink-soft); flex: none; }
  .contact .web { margin-top: 22px; margin-left: 21px; }

  .address {
    position: absolute; right: 90px; top: 258px;
    text-align: right; font-size: 14px; line-height: 19px;
    border-top: 1px solid var(--rule);
    padding-top: 8px; width: 230px;
  }

  .sweep { position: absolute; left: 0; bottom: 0; width: 640px; height: 366px; pointer-events: none; }
</style>
</head>
<body>

<section class="card card--front" aria-label="Card front">
  <div class="brand"><span class="brand__dot"></span>Marlow Sail Works</div>
</section>

<section class="card card--back" aria-label="Card back">
  <svg class="sweep" viewBox="0 0 640 366" aria-hidden="true">
    <defs>
      <linearGradient id="silver" x1="0" y1="0" x2="1" y2="0">
        <stop offset="0" stop-color="var(--silver-light)"/>
        <stop offset="0.55" stop-color="var(--silver-dark)"/>
        <stop offset="1" stop-color="#1a1a1a"/>
      </linearGradient>
    </defs>
    <path d="M0 286 C 120 300, 300 330, 620 366 L 0 366 Z" fill="url(#silver)"/>
    <path d="M0 300 C 140 316, 320 344, 560 366 L 0 366 Z" fill="var(--card)"/>
  </svg>

  <div class="brand"><span class="brand__dot"></span>Marlow Sail Works</div>

  <div class="person">
    <div class="person__name">Dean Pellway</div>
    <div class="person__title">President</div>
  </div>

  <div class="rule"></div>

  <ul class="contact">
    <li><svg viewBox="0 0 12 12"><path d="M2 0h3l1 3-2 1c1 2 2 3 4 4l1-2 3 1v3c0 1-1 2-2 2C5 12 0 7 0 2 0 1 1 0 2 0z"/></svg>731.508.2164</li>
    <li><svg viewBox="0 0 12 12"><path d="M3 0h6a1 1 0 0 1 1 1v10a1 1 0 0 1-1 1H3a1 1 0 0 1-1-1V1a1 1 0 0 1 1-1zm0 2v7h6V2z"/></svg>731.508.2270</li>
    <li><svg viewBox="0 0 12 12"><path d="M3 0h6v3H3zM0 4h12v5h-2v3H2V9H0zm3 4v3h6V8z"/></svg>731.508.2391</li>
    <li><svg viewBox="0 0 12 12"><path d="M0 2h12v1L6 7 0 3zm0 2l6 4 6-4v6H0z"/></svg>info@marlowsail.com</li>
  </ul>

  <div class="address">
    412 Harbor Reach Road<br>
    Newport, Rhode Island 02840<br>
    www.marlowsail.com
  </div>
</section>

</body>
</html>
```